Business cards to launch an education platform

Hi,
I am looking at having new business cards designed.
I am a startup, developing a web platform for schools and university, the education world. It's an online assessment system.
I would like a card that looks classy, and that is using the colors and the font of my logo.

I have attached:
1) my logo
2) A business card that I have designed quickly so you can have all the information required in the card, but I really don't like it.
3) The font that I am using (Lato Regular) to design my web platform
4) Some screenshots of my web platform so you can have a look at the style that I have.

Target Market(s)

Major market: Education system: Schools and university
Minor markets: Business in general

Industry/Entity Type

Business

Contact Information for Business Card

Clara Fenwick
Director

M: 0437 518 902
E: clara.fenwick@amberLoomSystems.com.au

Requirements
Must have
• The colors of my logo

```html
<!DOCTYPE html>
<html lang="en">
<head>
<meta charset="utf-8">
<title>Amber Loom Systems — Business Cards</title>
<link rel="stylesheet" href="https://fonts.googleapis.com/css2?family=Lato:wght@400;700&display=swap">
<style>
  :root {
    --navy: #1b3764;
    --navy-deep: #16305a;
    --sky: #2e9fe0;
    --ink: #3d4148;
    --rule: #d9dde3;
    --paper: #ffffff;
    --backdrop: #e9ebef;
    --ghost: #eef0f4;
  }
  * { margin: 0; padding: 0; box-sizing: border-box; }
  html, body {
    width: 1200px;
    height: 675px;
    overflow: hidden;
    background: var(--backdrop);
    font-family: "Lato", sans-serif;
  }
  .canvas {
    position: relative;
    width: 1200px;
    height: 675px;
  }
  .card {
    position: absolute;
    top: 183px;
    width: 540px;
    height: 309px;
    overflow: hidden;
    box-shadow: 0 10px 28px rgba(20, 30, 50, 0.18);
  }

  /* Back of card */
  .card-back {
    left: 40px;
    background: var(--navy);
  }
  .card-back .brand {
    position: absolute;
    top: 92px;
    left: 0;
    width: 100%;
    display: flex;
    flex-direction: column;
    align-items: center;
    gap: 14px;
  }
  .card-back .brand-mark {
    width: 46px;
    height: 46px;
    background: var(--sky);
  }
  .card-back .brand-name {
    color: var(--sky);
    font-size: 22px;
    font-weight: 400;
    letter-spacing: 0.5px;
  }
  .card-back .web {
    position: absolute;
    bottom: 40px;
    left: 0;
    width: 100%;
    text-align: center;
    color: #ffffff;
    font-size: 13px;
  }
  .card-back .web .web-name { color: var(--sky); }

  /* Front of card */
  .card-front {
    left: 620px;
    background: var(--paper);
  }
  .card-front .ghost-block {
    position: absolute;
    right: 40px;
    top: 60px;
    width: 210px;
    height: 230px;
    background: var(--ghost);
  }
  .card-front .brand {
    position: absolute;
    top: 30px;
    left: 34px;
    display: flex;
    flex-direction: column;
    gap: 10px;
  }
  .card-front .brand-mark {
    width: 40px;
    height: 40px;
    background: var(--navy);
  }
  .card-front .brand-name {
    color: var(--navy);
    font-size: 19px;
    font-weight: 400;
    letter-spacing: 0.6px;
  }
  .card-front .divider {
    position: absolute;
    left: 34px;
    right: 34px;
    height: 1px;
    background: var(--rule);
  }
  .card-front .divider-top { top: 158px; }
  .card-front .divider-bottom { top: 252px; left: 300px; }
  .card-front .contact {
    position: absolute;
    top: 172px;
    left: 34px;
    list-style: none;
    display: flex;
    flex-direction: column;
    gap: 7px;
    color: var(--ink);
    font-size: 12.5px;
  }
  .card-front .contact li {
    display: flex;
    align-items: center;
    gap: 8px;
  }
  .card-front .contact svg {
    width: 11px;
    height: 11px;
    flex: none;
  }
  .card-front .person {
    position: absolute;
    right: 34px;
    top: 206px;
    text-align: right;
  }
  .card-front .person-name {
    color: var(--navy);
    font-size: 18px;
    font-weight: 400;
  }
  .card-front .person-role {
    color: var(--sky);
    font-size: 12.5px;
    margin-top: 1px;
  }
</style>
</head>
<body>
<main class="canvas">

  <section class="card card-back" aria-label="Business card back">
    <div class="brand">
      <div class="brand-mark"></div>
      <div class="brand-name">Amber Loom Systems</div>
    </div>
    <p class="web">www.<span class="web-name">AmberLoomSystems</span>.com.au</p>
  </section>

  <section class="card card-front" aria-label="Business card front">
    <div class="ghost-block"></div>

    <div class="brand">
      <div class="brand-mark"></div>
      <div class="brand-name">Amber Loom Systems</div>
    </div>

    <div class="divider divider-top"></div>

    <ul class="contact">
      <li>
        <svg viewBox="0 0 12 12" aria-hidden="true"><rect x="3" y="0.5" width="6" height="11" rx="1.2" fill="none" stroke="#2e9fe0" stroke-width="1.1"/><circle cx="6" cy="9.6" r="0.7" fill="#2e9fe0"/></svg>
        <span>0437 518 902</span>
      </li>
      <li>
        <svg viewBox="0 0 12 12" aria-hidden="true"><rect x="0.5" y="2.5" width="11" height="7.5" fill="#2e9fe0"/><path d="M0.8 2.8 L6 7 L11.2 2.8" fill="none" stroke="#ffffff" stroke-width="1"/></svg>
        <span>clara.fenwick@amberLoomSystems.com.au</span>
      </li>
      <li>
        <svg viewBox="0 0 12 12" aria-hidden="true"><circle cx="6" cy="6" r="5.2" fill="none" stroke="#2e9fe0" stroke-width="1"/><ellipse cx="6" cy="6" rx="2.3" ry="5.2" fill="none" stroke="#2e9fe0" stroke-width="0.9"/><line x1="0.8" y1="6" x2="11.2" y2="6" stroke="#2e9fe0" stroke-width="0.9"/></svg>
        <span>www.amberLoomSystems.com.au</span>
      </li>
    </ul>

    <div class="person">
      <div class="person-name">Clara Fenwick</div>
      <div class="person-role">Director</div>
    </div>

    <div class="divider divider-bottom"></div>
  </section>

</main>
</body>
</html>
```